DOUBLE SIDED BROCHURE NEEDED TO PROMOTE DOCTOR

I need a double sided DL size (99mm x 210mm) brochure, promoting a doctor seeing patients in a new area.

I want something professional. I have included the relevant information. I would also like the Dr's picture somwhere in the brochure, with a professional background. I wish to print these tomorrow, so i will pick a winner within 14 hours of posting this ad.

I have included an example of a brochures design that I recently saw, and its definietly a good starting point.

Industry/Entity Type

Medical

```html
<!DOCTYPE html>
<html lang="en">
<head>
<meta charset="utf-8">
<title>Dr Haddad – Mandurah Consulting Brochure</title>
<link href="https://fonts.googleapis.com/css2?family=Cardo:wght@400;700&family=Marcellus+SC&display=swap" rel="stylesheet">
<style>
  :root {
    --page: #e6e7e9;
    --navy: #1d3d8c;
    --ink: #0d1a3a;
    --sky: #2db3e8;
    --sky-deep: #1787d3;
    --sky-light: #55c6ec;
    --pale-top: #e6f6fb;
    --pale-bottom: #c7eaf6;
    --grey-band: #a9adb2;
    --white: #ffffff;
  }
  * { box-sizing: border-box; margin: 0; padding: 0; }
  html, body { width: 849px; height: 1200px; overflow: hidden; }
  body { background: var(--page); position: relative; font-family: "Cardo", serif; }

  .panel {
    position: absolute; top: 197px; width: 380px; height: 806px; overflow: hidden;
    box-shadow: 0 6px 18px rgba(0,0,0,.18);
  }

  /* Back side */
  .panel--back { left: 29px; background: linear-gradient(180deg, var(--pale-top), var(--pale-bottom)); }
  .back__top-grey { height: 12px; background: var(--grey-band); }
  .back__top-band { height: 26px; background: var(--sky); }
  .back__bottom-band { position: absolute; bottom: 0; left: 0; right: 0; height: 26px; background: var(--sky); }
  .back__content { padding: 26px 26px 0 26px; color: var(--ink); }
  .heading {
    font-family: "Marcellus SC", serif; color: var(--navy); letter-spacing: .5px;
  }
  .back__greeting { font-size: 24px; margin-bottom: 6px; }
  .back__intro { font-size: 16.5px; line-height: 1.45; text-align: justify; margin-bottom: 26px; }
  .back__specialty { font-size: 21px; line-height: 1.35; margin-bottom: 20px; }
  .ticks { list-style: none; margin-bottom: 22px; }
  .ticks li { display: flex; align-items: flex-start; gap: 10px; font-size: 18px; line-height: 1.2; margin-bottom: 12px; }
  .ticks small { display: block; font-size: 14px; }
  .ticks svg { flex: none; margin-top: 3px; }
  .general__title { font-size: 19px; margin-bottom: 8px; }
  .general { list-style: none; padding-left: 22px; }
  .general li { font-family: "Marcellus SC", serif; font-size: 16px; line-height: 1.55; }
  .general li::before { content: "\2022"; margin-right: 8px; }

  /* Front side */
  .panel--front { left: 439px; background: linear-gradient(180deg, var(--sky) 0%, var(--sky-deep) 100%); }
  .front__art { position: absolute; top: 0; left: 0; }
  .front__title {
    position: absolute; top: 490px; left: 54px; right: 0; padding: 10px 10px 10px 0;
    background: var(--sky-light); text-align: right; box-shadow: 0 3px 6px rgba(0,0,0,.25);
    font-family: "Marcellus SC", serif; font-size: 25px; line-height: 1.3; color: var(--ink); letter-spacing: 1px;
  }
  .front__clinic { position: absolute; top: 640px; right: 10px; text-align: left; }
  .clinic__label { font-family: "Marcellus SC", serif; font-size: 20px; color: var(--ink); text-align: right; margin-bottom: 8px; }
  .clinic__address { font-size: 19px; line-height: 1.1; font-weight: 700; color: var(--ink); padding-left: 4px; }
  .front__referral {
    position: absolute; bottom: 0; left: 0; right: 0; height: 34px;
    background: linear-gradient(180deg, rgba(255,255,255,0) 0%, rgba(160,165,170,.9) 100%);
    font-family: "Marcellus SC", serif; font-size: 13px; color: var(--white);
    display: flex; align-items: center; justify-content: center;
  }
</style>
</head>
<body>

<section class="panel panel--back">
  <div class="back__top-grey"></div>
  <div class="back__top-band"></div>
  <div class="back__content">
    <h2 class="heading back__greeting">Dear Doctors,</h2>
    <p class="back__intro">We are pleased to announce that Dr.KarimHaddad is now consulting in Mandurah, seeing public and private patients. Guaranteed appointment within two weeks, with patients having the option of surgery at Coastal Health Campus, Harbourview Hospital or St. Brendan's Southgate.</p>
    <h2 class="heading back__specialty">Dr.Haddad is a highly specialised surgeon in the areas of endocrine &amp; general surgery</h2>
    <ul class="ticks">
      <li><svg width="18" height="18" viewBox="0 0 18 18"><circle cx="9" cy="9" r="7.5" fill="none" stroke="#6b6f75" stroke-width="2"/><path d="M5 9.5l3 3 5-6" fill="none" stroke="#6b6f75" stroke-width="2"/></svg><span>Thyroid Surgery</span></li>
      <li><svg width="18" height="18" viewBox="0 0 18 18"><circle cx="9" cy="9" r="7.5" fill="none" stroke="#6b6f75" stroke-width="2"/><path d="M5 9.5l3 3 5-6" fill="none" stroke="#6b6f75" stroke-width="2"/></svg><span>Parathyroid Surgery<small>(including minimally invasive)</small></span></li>
      <li><svg width="18" height="18" viewBox="0 0 18 18"><circle cx="9" cy="9" r="7.5" fill="none" stroke="#6b6f75" stroke-width="2"/><path d="M5 9.5l3 3 5-6" fill="none" stroke="#6b6f75" stroke-width="2"/></svg><span>Breast Cancer Surgery</span></li>
    </ul>
    <p class="general__title">All areas of general surgery:</p>
    <ul class="general">
      <li>Gallbladder</li>
      <li>Hernia</li>
      <li>Haemorrhoids</li>
      <li>Colonoscopy</li>
      <li>Varicose Veins</li>
    </ul>
  </div>
  <div class="back__bottom-band"></div>
</section>

<section class="panel panel--front">
  <svg class="front__art" width="380" height="806" viewBox="0 0 380 806">
    <defs>
      <linearGradient id="photoTone" x1="0" y1="0" x2="0" y2="1">
        <stop offset="0" stop-color="#8cc4ea"/>
        <stop offset="0.45" stop-color="#dbe7f0"/>
        <stop offset="1" stop-color="#5d6a72"/>
      </linearGradient>
    </defs>
    <ellipse cx="150" cy="245" rx="232" ry="292" fill="#ffffff"/>
    <ellipse cx="138" cy="236" rx="222" ry="286" fill="url(#photoTone)" role="img" aria-label="Photo of the doctor smiling in front of a modern hospital building under a blue sky"/>
  </svg>
  <h1 class="front__title">Dr.KarimHaddad is now<br>consulting in<br>Mandurah</h1>
  <div class="front__clinic">
    <p class="clinic__label">Mandurah Clinic:</p>
    <p class="clinic__address">42 Ellery Road<br>Mandurah WA 6210.<br>Phone: 1300 000 418</p>
  </div>
  <p class="front__referral">Please send all referrals by fax to (08) 6000 2471</p>
</section>

</body>
</html>
```